Business Card: RW Office Partners - Your organised problem solver

Business Name: RW Office Partners
Website: www.rwofficepartners.com.au
Email: marisol@rwofficepartners.com.au
Mobile: 61 482 907 236
Facebook: @rwofficepartners
Instrgram: @rwofficepartners

Brading Colours:
HEX
#986474
#ddccd3
#7a8498
#c9d8e4
#000000
#ffffff

Tag Line: Your organised problem solver

Link to DRAFT website:
https://deskhelpcollective.wixsite.com/rw-office-partners

About Page from the website:
My name is Marisol Wrenfield, and I would love to assist you to become more productive in your day to day and achieve your business and personal goals.
My mission is to give you time, time to work on the important tasks of your business or to be able to spend more time with your family. I will take on the tasks you don’t have time for, don’t know well or simply don’t like to do.
I have an extensive background in Administration, Tender Coordination, Document Control, WHS and Quality Management working primarily in the Construction, Mining and Corporate World.
I am passionate about being organised, having order and making things in your life (and mine) easier! I love to watch something unfold and grow into something amazing! I am known for being the go-to problem solver, the organiser of all things, producing high standards of work even under pressure. I’m also a confident communicator, and I understand that you’re busy running your business.

Target Market(s)

Small to Medium Business who require assistance in their business by a virtual assistant.

Industry/Entity Type

Virtual Assistant

Contact Information for Business Card

Mobile: 61 482 907 236

Font styles to use
Sans Serif

Colors
ffffff

Requirements
Must have
• Branding Colours as outlined.
Contact Details as outlined.
Logo as provided.
Proper contact details - mobile, facebook, instragm, website.
Simple, Elegant, very clean looking.
Should not have
• Note cute with pictures.
Not too girly as still want to market to construction companies.

```html
<!DOCTYPE html>
<html lang="en">
<head>
<meta charset="utf-8">
<title>RW Office Partners – Business Card</title>
<link href="https://fonts.googleapis.com/css2?family=Roboto:wght@400;500;700&display=swap" rel="stylesheet">
<style>
  :root {
    --mauve: #986474;
    --mauve-light: #ddccd3;
    --slate: #7a8498;
    --slate-light: #c9d8e4;
    --card: #1d1b20;
    --stage: #3a3a3c;
    --white: #ffffff;
    --embossed: #5e5e63;
  }
  * { box-sizing: border-box; margin: 0; padding: 0; }
  html, body {
    width: 799px; height: 1200px; overflow: hidden;
    background: var(--stage);
    font-family: "Roboto", Arial, sans-serif;
  }
  .card {
    position: absolute; left: 80px; width: 640px; height: 366px;
    background: var(--card); overflow: hidden;
    box-shadow: 0 10px 30px rgba(0,0,0,.45);
  }
  .card--front { top: 140px; }
  .card--back  { top: 694px; }

  /* Front */
  .front-brand {
    position: absolute; left: 0; right: 0; top: 120px;
    text-align: center; font-size: 50px; font-weight: 500;
    color: var(--embossed); letter-spacing: 1px;
  }
  .social-row {
    position: absolute; left: 0; right: 0; top: 260px;
    display: flex; justify-content: center; gap: 28px;
    color: var(--white); font-size: 18px;
  }
  .social { display: flex; align-items: center; gap: 8px; }
  .social-mark {
    width: 13px; height: 13px; border-radius: 2px; background: var(--mauve);
  }

  /* Back */
  .back-brand {
    position: absolute; right: 34px; top: 38px;
    font-size: 40px; font-weight: 500; color: var(--slate);
  }
  .person { position: absolute; left: 36px; top: 140px; }
  .person-name { font-size: 24px; font-weight: 700; color: var(--mauve); }
  .person-role { font-size: 15px; color: var(--white); margin-top: 4px; }
  .back-socials {
    position: absolute; left: 36px; top: 212px;
    display: flex; flex-direction: column; gap: 6px;
    color: var(--white); font-size: 15px;
  }
  .contact {
    position: absolute; left: 330px; top: 200px;
    display: flex; flex-direction: column; gap: 7px;
    color: var(--white); font-size: 16px;
  }
  .contact-line { display: flex; align-items: center; gap: 10px; }
  .contact-line svg { width: 14px; height: 14px; flex: none; }
  .band-slate {
    position: absolute; left: 0; top: 282px; width: 280px; height: 14px;
    background: var(--slate);
  }
  .band-mauve {
    position: absolute; left: 250px; right: 0; top: 282px; bottom: 0;
    background: var(--mauve); border-top-left-radius: 34px;
    display: flex; align-items: center; padding-left: 40px;
    color: var(--white); font-size: 19px;
  }
</style>
</head>
<body>
  <section class="card card--front" aria-label="Business card front">
    <div class="front-brand">RW Office Partners</div>
    <div class="social-row">
      <span class="social"><span class="social-mark"></span>@rwofficepartners</span>
      <span class="social"><span class="social-mark"></span>@rwofficepartners</span>
    </div>
  </section>

  <section class="card card--back" aria-label="Business card back">
    <div class="back-brand">RW Office Partners</div>
    <div class="person">
      <div class="person-name">Marisol Wrenfield</div>
      <div class="person-role">Virtual Assistant</div>
    </div>
    <div class="back-socials">
      <span class="social"><span class="social-mark"></span>@rwofficepartners</span>
      <span class="social"><span class="social-mark"></span>@rwofficepartners</span>
    </div>
    <div class="contact">
      <div class="contact-line">
        <svg viewBox="0 0 16 16" aria-hidden="true"><path fill="#986474" d="M3 1h3l1 4-2 1a9 9 0 0 0 5 5l1-2 4 1v3a2 2 0 0 1-2 2A13 13 0 0 1 1 3a2 2 0 0 1 2-2z"/></svg>
        61 482 907 236
      </div>
      <div class="contact-line">
        <svg viewBox="0 0 16 16" aria-hidden="true"><rect x="1" y="3" width="14" height="10" fill="#986474"/><path d="M1 3l7 6 7-6" fill="none" stroke="#1d1b20" stroke-width="1.5"/></svg>
        marisol@rwofficepartners.com.au
      </div>
      <div class="contact-line">
        <svg viewBox="0 0 16 16" aria-hidden="true"><g fill="none" stroke="#986474" stroke-width="1.6"><circle cx="8" cy="8" r="6.5"/><ellipse cx="8" cy="8" rx="3" ry="6.5"/><path d="M1.5 8h13"/></g></svg>
        www.rwofficepartners.com.au
      </div>
    </div>
    <div class="band-slate"></div>
    <div class="band-mauve">Your organised problem solver</div>
  </section>
</body>
</html>
```